KRL Stationery Design Project

Dear Designers,
We need a new stationery design for company to match our new logo.
Designers should provide a design for the following:
1. Business Card: 3.5x2 Inches.
2. Letterhead: A4 size.
3. Envelops: 25x35.5 Cm.
You can keep the Arabic name at the bottom of the logo Or you can use the separate attached Arabic Name.
Please refer to the attached logo guide for design information.
Sample Business Card information:
Name: Tarek Sowan
Position: Operation Manager
Tel: +966 920007164 Ex. 500
Fax: +966 (3)8842617
Mob: +966 (5)00263817
email: tarek@krl-example.com.sa
URL: www.krl-example.com.sa
Address:
Nakheel Heights, Suite 718
Zayed bin Omar Str.
Khobar, 31847
Saudi Arabia
Updates
Dear All,
Please note, we had uploaded our logo along with Arabic writing in Adobe illustrator format (.ai).
Regards,
Karim
Dear All,
A sample data for the business card had been added as per your request.
Regards,
Karim

```html
<!DOCTYPE html>
<html lang="en">
<head>
<meta charset="utf-8">
<title>KRL Letterhead</title>
<link href="https://fonts.googleapis.com/css2?family=Titillium+Web:wght@400;700&display=swap" rel="stylesheet">
<style>
  :root {
    --navy: #14294a;
    --ink: #3a3a3c;
    --band: #6d6e71;
    --paper: #ffffff;
    --edge: #b9b9b9;
  }
  * { margin: 0; padding: 0; box-sizing: border-box; }
  html, body { width: 848px; height: 1200px; overflow: hidden; background: var(--paper); }
  .letterhead {
    position: relative;
    width: 848px;
    height: 1200px;
    background: var(--paper);
    border: 1px solid var(--edge);
    font-family: "Titillium Web", sans-serif;
    color: var(--ink);
  }
  .brand {
    position: absolute;
    top: 42px;
    right: 28px;
    width: 270px;
    height: 76px;
    display: flex;
    align-items: center;
    justify-content: center;
    gap: 12px;
  }
  .brand-dot {
    width: 18px;
    height: 18px;
    border-radius: 50%;
    background: var(--navy);
  }
  .brand-name {
    font-size: 52px;
    font-weight: 700;
    color: var(--navy);
    line-height: 1;
    letter-spacing: 2px;
  }
  .contacts {
    position: absolute;
    top: 127px;
    left: 632px;
    list-style: none;
  }
  .contacts li {
    display: flex;
    align-items: center;
    height: 22px;
    font-size: 14px;
    line-height: 1;
  }
  .contacts svg {
    width: 17px;
    height: 15px;
    margin-right: 12px;
    flex: none;
  }
  .footer-band {
    position: absolute;
    left: 23px;
    right: 22px;
    top: 1145px;
    height: 27px;
    background: var(--band);
    color: #fff;
    font-size: 14px;
    letter-spacing: 4.2px;
    display: flex;
    align-items: center;
    justify-content: center;
    white-space: nowrap;
  }
</style>
</head>
<body>
<div class="letterhead">
  <div class="brand">
    <span class="brand-dot"></span>
    <span class="brand-name">KRL</span>
  </div>

  <ul class="contacts">
    <li>
      <svg viewBox="0 0 17 15" aria-hidden="true"><path d="M1 5 Q8.5 0 16 5 L14 7 L12 5.5 L5 5.5 L3 7 Z" fill="none" stroke="#222" stroke-width="1.4"/><rect x="3.5" y="7" width="10" height="7" rx="1" fill="none" stroke="#222" stroke-width="1.4"/><circle cx="8.5" cy="10.5" r="1.6" fill="#222"/></svg>
      +966 920007164 Ex. 500
    </li>
    <li>
      <svg viewBox="0 0 17 15" aria-hidden="true"><rect x="4.5" y="0.8" width="8" height="5" fill="none" stroke="#222" stroke-width="1.4"/><rect x="1.5" y="5.8" width="14" height="6" fill="none" stroke="#222" stroke-width="1.4"/><rect x="4.5" y="10" width="8" height="4.2" fill="#fff" stroke="#222" stroke-width="1.4"/></svg>
      +966 (3)8842617
    </li>
    <li>
      <svg viewBox="0 0 17 15" aria-hidden="true"><rect x="1" y="2.5" width="15" height="10" fill="none" stroke="#222" stroke-width="1.4"/><path d="M1 2.5 L8.5 8.5 L16 2.5 M1 12.5 L6.5 7 M16 12.5 L10.5 7" fill="none" stroke="#222" stroke-width="1.4"/></svg>
      tarek@krl-example.com.sa
    </li>
    <li>
      <svg viewBox="0 0 17 15" aria-hidden="true"><circle cx="8.5" cy="7.5" r="6.8" fill="#222"/><path d="M5 3.5 Q7 5 6 7 Q4.5 8 5.5 10 M10 2 Q12 4.5 11 6.5 Q13 8.5 12.5 11" fill="none" stroke="#fff" stroke-width="1.3"/></svg>
      www.krl-example.com.sa
    </li>
  </ul>

  <div class="footer-band">Nakheel Heights, Suite 718, Zayed bin Omar Str., Khobar, 31847, Saudi Arabia</div>
</div>
</body>
</html>
```